New hardcover book cover

I want a striking, eye-catching cover with title, subtitle and a picture.See for previous book covers: www.brightquillpress.com

Target Market(s)

young, successful entrepreneurs that have built a business in a niche market that they discovered.

Font styles to use
Serif

Colors

Designer to choose colors to be used in the design.

Requirements
Must have
• A book cover that impresses and captures the imagination of those who look at it.
• MY MISTAKE, SORRY.
• Title: Founders Behind the Quiet Trade Boom
• Subtitle: 25 stories of success from
• discovering hidden opportunities
• Author: Dennis Harlow
• Please use the photo attached, thanks.

```html
<!DOCTYPE html>
<html lang="en">
<head>
<meta charset="utf-8">
<title>Founders Behind the Quiet Trade Boom — Dennis Harlow</title>
<link rel="stylesheet" href="https://fonts.googleapis.com/css2?family=Montserrat:wght@300;400;800;900&display=swap">
<style>
  :root {
    --navy: #14182a;
    --steel: #3c4460;
    --sky: #9fc4e4;
    --sky-deep: #5f8fc0;
    --target-red: #c8284a;
    --white: #ffffff;
  }
  * { margin: 0; padding: 0; box-sizing: border-box; }
  html, body { width: 764px; height: 1200px; overflow: hidden; background: var(--navy); }
  .cover {
    position: relative;
    width: 764px;
    height: 1200px;
    overflow: hidden;
    font-family: "Montserrat", sans-serif;
    color: var(--white);
  }
  .cover-photo {
    position: absolute;
    inset: 0;
    background:
      radial-gradient(ellipse 62% 48% at 8% 50%, var(--target-red) 0%, #a01f3e 40%, rgba(40,30,50,0) 72%),
      linear-gradient(112deg, var(--navy) 0%, var(--steel) 48%, var(--sky-deep) 72%, var(--sky) 100%);
  }
  .cover-photo::after {
    content: "";
    position: absolute;
    inset: 0;
    background: linear-gradient(180deg, rgba(10,12,24,0.35) 0%, rgba(10,12,24,0) 25%, rgba(10,12,24,0) 55%, rgba(10,12,24,0.55) 100%);
  }
  .author {
    position: absolute;
    top: 84px;
    left: 0;
    width: 100%;
    text-align: center;
    padding-left: 18px;
    font-weight: 300;
    font-size: 40px;
    letter-spacing: 0.2em;
    text-transform: uppercase;
  }
  .title {
    position: absolute;
    top: 742px;
    left: 140px;
    width: 500px;
    text-align: center;
    text-transform: uppercase;
    font-weight: 900;
    line-height: 1;
    letter-spacing: -0.02em;
  }
  .title-line { display: block; white-space: nowrap; }
  .title-lead { font-size: 74px; }
  .title-mid { font-size: 70px; margin-top: 4px; display: flex; justify-content: center; align-items: center; gap: 6px; }
  .title-small { display: inline-flex; flex-direction: column; font-size: 24px; line-height: 0.95; letter-spacing: 0; text-align: center; }
  .title-rule { font-size: 70px; margin-top: 8px; display: flex; justify-content: center; align-items: center; gap: 18px; }
  .title-rule .dash { display: inline-block; width: 78px; height: 7px; background: var(--white); }
  .title-end { font-size: 88px; margin-top: 8px; }
  .subtitle {
    position: absolute;
    top: 1116px;
    left: 0;
    width: 100%;
    padding-left: 18px;
    text-align: center;
    text-transform: uppercase;
    font-weight: 400;
    font-size: 22px;
    line-height: 1.45;
  }
</style>
</head>
<body>
  <main class="cover">
    <div class="cover-photo" role="img" aria-label="Photograph of a dart striking the red bullseye of a target, with blue sky behind"></div>
    <p class="author">Dennis Harlow</p>
    <h1 class="title">
      <span class="title-line title-lead">Founders</span>
      <span class="title-line title-mid"><span class="title-small"><span>Behind</span><span>the</span></span>Quiet</span>
      <span class="title-line title-rule"><span class="dash"></span>Trade<span class="dash"></span></span>
      <span class="title-line title-end">Boom</span>
    </h1>
    <p class="subtitle">25 captivating stories of success<br>from discovering hidden opportunities</p>
  </main>
</body>
</html>
```